Bluecrest Learning Corps by graduating students from college in two years

Based on the logo design, create stationary and business cards for
Dr. Venrel T Oskamp, CEO, (555) 482-1736
and Marisa Deltoft, Respresentative, (555) 647-2208
Address: 4719 Pellham Court, Brenmoor Station, VA 20417
Incorporate elelments of the logo

Target Market(s)

USA

Font styles to use
Other font styles liked:
• match with the logo type style

```html
<!DOCTYPE html>
<html lang="en">
<head>
<meta charset="utf-8">
<title>Bluecrest Learning Corps Letterhead</title>
<link href="https://fonts.googleapis.com/css2?family=Arimo:wght@400;700&family=Montserrat:wght@600;700&display=swap" rel="stylesheet">
<style>
  :root {
    --navy: #1b2a5e;
    --gold: #f4c22b;
    --ink: #3a3a3a;
    --muted: #5a5a5a;
    --rule: #8a8a8a;
    --paper: #ffffff;
    --backdrop: #e9e9ea;
  }
  * { margin: 0; padding: 0; box-sizing: border-box; }
  html, body { width: 1200px; height: 960px; overflow: hidden; }
  body {
    background: var(--backdrop);
    display: flex; align-items: center; justify-content: center;
    font-family: "Arimo", Arial, sans-serif;
    color: var(--ink);
  }
  .letterhead {
    position: relative;
    width: 696px; height: 900px;
    background: var(--paper);
    box-shadow: 0 6px 22px rgba(0,0,0,0.12);
    overflow: hidden;
  }
  .brand {
    position: absolute; left: 40px; top: 44px;
    display: flex; align-items: center; gap: 10px;
    width: 170px;
  }
  .brand-dot {
    flex: none; width: 26px; height: 26px; border-radius: 50%;
    background: var(--gold);
  }
  .brand-name {
    font-family: "Montserrat", Arial, sans-serif;
    font-weight: 700; font-size: 15px; line-height: 1.2;
    color: var(--navy);
  }
  .header-rule {
    position: absolute; left: 214px; right: 36px; top: 108px;
    border-top: 1px solid var(--rule);
  }
  .contacts {
    position: absolute; left: 220px; top: 40px;
    display: flex; align-items: flex-end; gap: 16px;
  }
  .contact { font-size: 11px; line-height: 1.3; color: var(--muted); }
  .contact-name {
    font-family: "Montserrat", Arial, sans-serif;
    font-weight: 700; font-size: 13px; color: var(--navy);
  }
  .contact-phone { display: flex; align-items: center; gap: 4px; }
  .contact-phone svg { width: 10px; height: 10px; fill: var(--gold); }
  .divider { width: 1px; height: 40px; background: var(--gold); }
  .address { font-size: 10.5px; line-height: 1.3; color: var(--muted); }
  .letter-body {
    position: absolute; left: 200px; right: 44px; top: 230px;
    font-size: 11.5px; line-height: 1.3; color: var(--muted);
  }
  .salutation {
    font-family: "Montserrat", Arial, sans-serif;
    font-weight: 700; font-size: 17px; color: var(--ink);
    margin-bottom: 16px;
  }
  .letter-body p { margin-bottom: 16px; }
  .closing { font-weight: 700; font-size: 10.5px; margin-top: 20px; color: var(--ink); }
  .signature {
    margin-top: 14px; margin-left: 40px;
    width: 120px; height: 34px; border-radius: 4px;
    background: linear-gradient(90deg, #ececec, #dcdcdc);
  }
  .footer-bands { position: absolute; left: 0; bottom: 0; width: 696px; height: 44px; }
</style>
</head>
<body>
  <main class="letterhead">
    <div class="brand">
      <span class="brand-dot"></span>
      <span class="brand-name">Bluecrest Learning Corps</span>
    </div>

    <div class="contacts">
      <div class="contact">
        <div class="contact-name">Dr. Venrel T Oskamp</div>
        <div>CEO</div>
        <div class="contact-phone"><svg viewBox="0 0 24 24"><path d="M6.6 10.8a15 15 0 0 0 6.6 6.6l2.2-2.2a1 1 0 0 1 1-.25 11.4 11.4 0 0 0 3.6.57 1 1 0 0 1 1 1V20a1 1 0 0 1-1 1A17 17 0 0 1 3 4a1 1 0 0 1 1-1h3.5a1 1 0 0 1 1 1c0 1.25.2 2.45.57 3.57a1 1 0 0 1-.25 1z"/></svg>(555) 482-1736</div>
      </div>
      <span class="divider"></span>
      <div class="contact">
        <div class="contact-name">Marisa Deltoft</div>
        <div>Respresentative</div>
        <div class="contact-phone"><svg viewBox="0 0 24 24"><path d="M6.6 10.8a15 15 0 0 0 6.6 6.6l2.2-2.2a1 1 0 0 1 1-.25 11.4 11.4 0 0 0 3.6.57 1 1 0 0 1 1 1V20a1 1 0 0 1-1 1A17 17 0 0 1 3 4a1 1 0 0 1 1-1h3.5a1 1 0 0 1 1 1c0 1.25.2 2.45.57 3.57a1 1 0 0 1-.25 1z"/></svg>(555) 647-2208</div>
      </div>
      <span class="divider"></span>
      <div class="address">4719 Pellham Court<br>Brenmoor Station<br>VA 20417</div>
    </div>
    <div class="header-rule"></div>

    <section class="letter-body">
      <div class="salutation">Dear Mr. Halvern,</div>
      <p>Lorem ipsum dolor sit amet, consectetuer adipiscing elit, sed diam nonummy nibh euismod tincidunt ut laoreet dolore magna aliquam erat volutpat. Ut wisi enim ad minim veniam, quis nostrud exerci tationmcorper suscipit lobortis nisl ut aliquip ex ea commodo consequat. Duis autem vel eum iriure dolor in hendrerit in vulputate velit esse molestie consequat, vel illum dolore eu feugiat</p>
      <p>Rorem ipsum dolor sit amet, consectetuer adipiscing elit, sed diam nonummy nibh euismod tincidunt ut laoreet dolore magna aliquam erat volutpat. Ut wisi enim ad minim veniam, quis nostrud exerci tationmcorper suscipit lobortis nisl ut aliquip ex ea commodo consequat. Duis autem vel eum iriure dolor in hendrerit in vulputate velit esse molest</p>
      <p>Dorem ipsum dolor sit amet, consectetuer adipiscing elit, sed diam nonummy nibh euismod tincidunt ut laoreet dolore magna aliquam erat volutpat. Ut wisi enim ad minim veniam, quis nostrud exerci tationmcorper suscipit lobortis nisl ut aliquip ex ea commodo consequat. Duis autem vel eum iriure dolor in hendrerit in suscipit lobortis nisl ut aliquip ex ea commodo consequat. Duis autem vel eum iriure dolor in hendrerit in vulputate velit esse molestie consequat, vel illum</p>
      <p>Sorem ipsum dolor sit amet, consectetuer adipiscing elit, sed diam nonummy nibh euismod tincidunt ut laoreet dolore magna aliquam erat volutpat. Ut wisi enim ad minim veniam, quis nostrud exerci tationmcorper suscipit lobortis nisl ut aliquip ex ea commodo consequat. Duis autem vel eum iriure dolor in</p>
      <div class="closing">Sincerely,</div>
      <div class="signature" role="img" aria-label="Handwritten signature"></div>
    </section>

    <svg class="footer-bands" viewBox="0 0 696 44" preserveAspectRatio="none">
      <polygon points="0,30 370,30 364,44 0,44" fill="var(--navy)"/>
      <polygon points="384,6 696,6 696,44 372,44" fill="var(--gold)"/>
    </svg>
  </main>
</body>
</html>
```